Health and wellnes company needs business cards

We are a Health and wellness business just relocated to Spain. Here nobody knows our business so we would like to put some of our services on the card. Clean design with logo.

Contact Information for Business Card

Brightmeadow
Paula & Oskar Dunbeck
Calle del Almendro 57
Villaroble del Mar
Mobile: 0046 731 402687
info@brightmeadow.example

Font styles to use
Serif

Colors
85cae6
85acd3
b768aa

Requirements
Must have
• these Services somewhere on the card
• - Private or group yoga
• - Reconnective healing
• - Kitesurfing lessons
• - Massage
• LOgo somewhere
Nice to have
• Colours that go with the logo please

```html
<!DOCTYPE html>
<html lang="en">
<head>
<meta charset="utf-8">
<title>Brightmeadow Business Card</title>
<link rel="stylesheet" href="https://fonts.googleapis.com/css2?family=PT+Serif:wght@400;700&display=swap">
<style>
  :root {
    --page-bg: #e4e4e2;
    --card-bg: #121213;
    --teal: #5fc2cb;
    --navy: #26497f;
    --white: #f2f2f2;
    --faint: #1f2326;
  }
  * { box-sizing: border-box; margin: 0; padding: 0; }
  html, body {
    width: 1200px; height: 900px; overflow: hidden;
    background: var(--page-bg);
    font-family: "PT Serif", Georgia, serif;
  }
  .canvas {
    width: 1200px; height: 900px;
    display: flex; flex-direction: column; align-items: center; justify-content: center;
    gap: 40px;
  }
  .card {
    position: relative;
    width: 700px; height: 400px;
    background: var(--card-bg);
    border-radius: 4px;
    box-shadow: 0 6px 18px rgba(0,0,0,0.25);
    overflow: hidden;
  }
  /* Front */
  .card--front {
    display: flex; flex-direction: column; align-items: center; justify-content: center; gap: 26px;
  }
  .brand-mark {
    width: 140px; height: 140px; border-radius: 50%;
    border: 14px solid var(--teal);
  }
  .brand-name--front {
    font-size: 50px; font-weight: 400; letter-spacing: 2px;
    color: var(--navy); text-transform: uppercase;
  }
  /* Back */
  .decor-circle {
    position: absolute; top: 22px; right: 72px;
    width: 190px; height: 190px; border-radius: 50%;
    border: 14px solid var(--faint);
  }
  .contact {
    position: absolute; left: 56px; bottom: 40px;
  }
  .brand-name--back {
    font-size: 38px; font-weight: 400; letter-spacing: 1.5px;
    color: var(--teal); text-transform: uppercase;
    margin-bottom: 34px;
  }
  .owners {
    font-size: 24px; font-weight: 700; color: var(--teal);
    margin-bottom: 10px;
  }
  .address { font-size: 17px; color: var(--white); line-height: 1.35; margin-bottom: 10px; }
  .contact-list { list-style: none; font-size: 17px; color: var(--white); line-height: 1.55; }
  .contact-list li { display: flex; align-items: center; gap: 10px; }
  .contact-list svg { width: 14px; height: 14px; fill: var(--teal); flex: none; }
  .web-domain { color: var(--teal); }
  .services {
    position: absolute; right: 56px; bottom: 48px;
    text-align: center; color: var(--teal);
  }
  .services-title { font-size: 23px; font-weight: 700; margin-bottom: 4px; }
  .services-list { list-style: none; font-size: 18px; line-height: 1.3; }
</style>
</head>
<body>
<main class="canvas">
  <section class="card card--front" aria-label="Card front">
    <div class="brand-mark"></div>
    <h1 class="brand-name--front">Brightmeadow</h1>
  </section>

  <section class="card card--back" aria-label="Card back">
    <div class="decor-circle"></div>
    <div class="contact">
      <h2 class="brand-name--back">Brightmeadow</h2>
      <p class="owners">Paula &amp; Oskar Dunbeck</p>
      <p class="address">Calle del Almendro 57<br>Villaroble del Mar</p>
      <ul class="contact-list">
        <li>
          <svg viewBox="0 0 24 24" aria-hidden="true"><path d="M6.6 10.8a15.1 15.1 0 0 0 6.6 6.6l2.2-2.2c.3-.3.7-.4 1-.2 1.1.4 2.3.6 3.6.6.6 0 1 .4 1 1V20c0 .6-.4 1-1 1A17 17 0 0 1 3 4c0-.6.4-1 1-1h3.5c.6 0 1 .4 1 1 0 1.3.2 2.5.6 3.6.1.3 0 .7-.2 1z"/></svg>
          0046 731 402687
        </li>
        <li>
          <svg viewBox="0 0 24 24" aria-hidden="true"><path d="M2 5h20v14H2zm2 2v.5l8 5 8-5V7zm0 2.8V17h16V9.8l-8 5z"/></svg>
          info@brightmeadow.example
        </li>
        <li>
          <svg viewBox="0 0 24 24" aria-hidden="true"><circle cx="12" cy="12" r="10"/></svg>
          <span>www.<span class="web-domain">brightmeadow.example</span></span>
        </li>
      </ul>
    </div>
    <div class="services">
      <h3 class="services-title">Our Services:</h3>
      <ul class="services-list">
        <li>Private or group yoga</li>
        <li>Reconnective healing</li>
        <li>Kitesurfing lessons</li>
        <li>Massage</li>
      </ul>
    </div>
  </section>
</main>
</body>
</html>
```